Business card design for a teacher - double sided, sleek design.

My name is Lina and I am an online Arabic language teacher. I am looking for a beautiful business card design for my online teaching business.

The cards will be printed in 85mm x 55mm size.
The card can be either portrait or landscape.

The design should contain my logo on one side and information on the other.

The design needs to be clean and modern. Use of subtle Arabic geometric patterns would be nice. Icons for the social media information on the card should also match the design theme.

My logo font is Consolas, which is a Monospace font.

Business card design should be delivered with editable PSD or EPS files in the handover.

Thanks

Lina

----

Information on the back:

URL: www.speakwithnadia.net [this should stand out more than other details]
Email: info@speakwithnadia.net
Instagram: @speakwithnadia
Facebook: facebook.com/speakwithnadia
Skype: speakwithnadia

My brand colours are shown in the logo attached. These are:
- Teal green - 4DC9C1
- Mango yellow - FFD600

Target Market(s)

- Young professionals
- Expatriates
- Women and Men

Industry/Entity Type

Education

Contact Information for Business Card

Information on the back:

Skype: speakwithnadia

- Teal green - 4DC9C1
- Mango yellow - FFD600

Font styles to use
Other font styles liked:
• Any font complimentary to my logo font which is a Monospace font called Consolas.

Colors

Designer to choose colors to be used in the design.

Requirements
Must have
• - Aesthetically pleasing look
• - Complimentary design with existing logo
Nice to have
• Arabic geometrical patterns

```html
<!DOCTYPE html>
<html lang="en">
<head>
<meta charset="utf-8">
<title>Speak with Nadia – Business Cards</title>
<link rel="stylesheet" href="https://fonts.googleapis.com/css2?family=Inconsolata:wght@400;700&display=swap">
<style>
  :root {
    --bg: #cfcfcf;
    --paper: #f3f3f3;
    --teal: #4dc9c1;
    --grey: #737373;
    --brown: #4a1f10;
    --ink: #111111;
  }
  * { margin: 0; padding: 0; box-sizing: border-box; }
  html, body { width: 1200px; height: 864px; overflow: hidden; }
  body {
    background: var(--bg);
    font-family: "Inconsolata", monospace;
    position: relative;
  }
  .card {
    position: absolute;
    width: 540px;
    height: 350px;
    background: var(--paper);
    box-shadow: 0 8px 24px rgba(0,0,0,0.18);
    overflow: hidden;
  }
  .card svg.card-art { position: absolute; inset: 0; }
  .card-info { left: 40px; top: 257px; }
  .card-brand { left: 620px; top: 257px; }

  .brand-name {
    position: absolute;
    left: 0; right: 0;
    text-align: center;
    font-family: "Inconsolata", monospace;
    font-weight: 700;
    font-size: 28px;
    letter-spacing: 2px;
    color: var(--grey);
    text-transform: uppercase;
    line-height: 1;
  }
  .card-info .brand-name { top: 70px; }
  .card-brand .brand-name { top: 128px; }

  .contact-list {
    position: absolute;
    left: 0; right: 0;
    top: 150px;
    list-style: none;
    text-align: center;
    font-size: 19px;
    line-height: 23px;
    color: var(--ink);
  }
  .contact-list .site { font-weight: 700; }

  .brand-url {
    position: absolute;
    left: 0; right: 0;
    top: 278px;
    text-align: center;
    font-size: 18px;
    color: var(--ink);
  }
</style>
</head>
<body>

  <section class="card card-info" aria-label="Card back with contact details">
    <svg class="card-art" width="540" height="350" viewBox="0 0 540 350" aria-hidden="true">
      <ellipse cx="270" cy="175" rx="258" ry="330" fill="none" stroke="var(--teal)" stroke-width="14"/>
      <ellipse cx="270" cy="175" rx="244" ry="318" fill="none" stroke="var(--grey)" stroke-width="7"/>
    </svg>
    <p class="brand-name">Speak with Nadia</p>
    <ul class="contact-list">
      <li>speakwithnadia</li>
      <li>@speakwithnadia</li>
      <li>facebook.com/speakwithnadia</li>
      <li>info@speakwithnadia.net</li>
      <li class="site">www.speakwithnadia.net</li>
    </ul>
  </section>

  <section class="card card-brand" aria-label="Card front with brand name">
    <svg class="card-art" width="540" height="350" viewBox="0 0 540 350" aria-hidden="true">
      <line x1="0" y1="62" x2="540" y2="62" stroke="var(--brown)" stroke-width="3"/>
      <rect x="0" y="72" width="540" height="140" fill="var(--grey)"/>
      <line x1="0" y1="222" x2="540" y2="222" stroke="var(--brown)" stroke-width="3"/>
      <ellipse cx="270" cy="175" rx="170" ry="250" fill="var(--paper)"/>
    </svg>
    <p class="brand-name">Speak with Nadia</p>
    <p class="brand-url">www.speakwithnadia.net</p>
  </section>

</body>
</html>
```